LLC needs a business card design that emphasizes consulting and expert witness in upstream oil and g

I need a business card design for my company called Obena Upstream Advisors, LLC. My expertise is in oil and gas upstream operations management to optimize performance and also as an expert witness for law firms in oil and gas upstream operations litigation.
The final design should communicate knowledge and hands-on experience as well as trust. (Obena means rope or lasso. Perhaps "Obena" should be in the form of a rope.) I do not like the color green in any shade. My first preference would be some shade of blue.
Industry/Entity Type
Oil And Gas

```html
<!DOCTYPE html>
<html lang="en">
<head>
<meta charset="utf-8">
<title>Obena Upstream Advisors, LLC — Business Card</title>
<link href="https://fonts.googleapis.com/css2?family=Arimo:wght@400;700&display=swap" rel="stylesheet">
<style>
  :root {
    --red-light: #d3473a;
    --red: #c1342b;
    --red-dark: #9e1f1b;
    --white: #ffffff;
    --paper: #f4f4f4;
    --navy: #1f3a8a;
    --stage: #e9e6e1;
    --rule: rgba(255,255,255,0.75);
  }
  * { box-sizing: border-box; margin: 0; padding: 0; }
  html, body { width: 1200px; height: 902px; overflow: hidden; }
  body {
    background: var(--stage);
    font-family: "Arimo", Arial, sans-serif;
    position: relative;
  }
  .card {
    position: absolute;
    width: 540px;
    height: 310px;
    top: 296px;
    overflow: hidden;
    box-shadow: 0 6px 18px rgba(0,0,0,0.18);
  }
  /* Front */
  .card-front {
    left: 40px;
    background: linear-gradient(135deg, var(--red-light) 0%, var(--red) 50%, var(--red-dark) 100%);
    display: flex;
    align-items: center;
    justify-content: center;
    padding: 0 40px;
  }
  .front-name {
    color: var(--white);
    font-weight: 700;
    font-size: 28px;
    letter-spacing: 0.2px;
    display: flex;
    align-items: center;
    gap: 12px;
    white-space: nowrap;
    margin-top: 40px;
  }
  .brand-dot {
    width: 12px; height: 12px; border-radius: 50%;
    background: var(--white);
    flex: none;
  }
  /* Back */
  .card-back {
    left: 620px;
    background: var(--paper);
  }
  .back-band {
    position: absolute;
    left: 0; right: 0;
    top: 78px;
    height: 160px;
    background: linear-gradient(135deg, var(--red-light) 0%, var(--red) 55%, var(--red-dark) 100%);
  }
  .back-name {
    position: absolute;
    left: 22px; top: 44px;
    color: var(--navy);
    font-weight: 700;
    font-size: 17px;
    white-space: nowrap;
  }
  .person {
    position: absolute;
    left: 100px; top: 148px;
    width: 220px;
    color: var(--white);
    text-align: center;
  }
  .person-name { font-size: 24px; font-weight: 400; }
  .person-title { font-size: 12px; margin-top: 3px; }
  .divider {
    position: absolute;
    left: 330px; top: 92px;
    width: 1px; height: 132px;
    background: var(--rule);
  }
  .contacts {
    position: absolute;
    left: 346px; top: 96px;
    width: 180px;
    list-style: none;
  }
  .contacts li {
    display: flex;
    align-items: center;
    gap: 8px;
    color: var(--white);
    font-size: 12px;
    padding: 6px 0 5px;
    border-bottom: 1px solid var(--rule);
    white-space: nowrap;
  }
  .contacts svg { width: 11px; height: 11px; flex: none; fill: var(--white); }
  .address {
    position: absolute;
    right: 22px; top: 256px;
    color: var(--navy);
    font-size: 13px;
    white-space: nowrap;
  }
</style>
</head>
<body>
  <section class="card card-front" aria-label="Card front">
    <p class="front-name"><span class="brand-dot"></span>Obena Upstream Advisors, LLC</p>
  </section>

  <section class="card card-back" aria-label="Card back">
    <p class="back-name">Obena Upstream Advisors, LLC</p>
    <div class="back-band"></div>
    <div class="person">
      <p class="person-name">Employee name</p>
      <p class="person-title">Managing Director</p>
    </div>
    <div class="divider"></div>
    <ul class="contacts">
      <li>
        <svg viewBox="0 0 24 24"><path d="M6.6 10.8a15 15 0 0 0 6.6 6.6l2.2-2.2c.3-.3.7-.4 1-.2 1.1.4 2.3.6 3.6.6.6 0 1 .4 1 1V20c0 .6-.4 1-1 1A17 17 0 0 1 3 4c0-.6.4-1 1-1h3.5c.6 0 1 .4 1 1 0 1.3.2 2.5.6 3.6.1.3 0 .7-.2 1z"/></svg>
        555-3018 2740
      </li>
      <li>
        <svg viewBox="0 0 24 24"><path d="M7 1h10a2 2 0 0 1 2 2v18a2 2 0 0 1-2 2H7a2 2 0 0 1-2-2V3a2 2 0 0 1 2-2zm0 3v14h10V4z"/></svg>
        555-7462 0913
      </li>
      <li>
        <svg viewBox="0 0 24 24"><path d="M2 3h20v13H2zm2 2v9h16V5zM8 19h8v2H8z"/></svg>
        www.obenaadvisors.com
      </li>
      <li>
        <svg viewBox="0 0 24 24"><path d="M2 5h20v14H2zm2 2v.5l8 5 8-5V7z"/></svg>
        hello@obenaadvisors.com
      </li>
    </ul>
    <p class="address">Your Address 14 Harlow Ave Millbrook,TX 00000</p>
  </section>
</body>
</html>
```